Clear Plastic Card Design

I am looking to have a business card designed from my logo icon. I am looking to match the style of a different business card I have attached in the files.
Looking for a card that is plastic, with layers of transparency in the shape of my logo icon (also attached in the files) - not a circle like the other card. The winning design will incorporate the red icon logo on the front and back and include the charity's name, "Light for the Weary Souls" in the same or similar font, as well as an email and phone number. For now, use the email: email@lightfortheweary-mail.org and the phone number 555-382-7194.
We like how the sample business card has transparency, partial and full opacity layers and a matching color scheme. Files will need to be in vector so that our business card printing company can work with it.
UPDATE:
We've some excellent designs in, thank you everyone! I got an early review from the owner, and he requested a minor redirect to find his perfect design. He wants the design to stand out by NOT being a rectangle. Try instead a circle, square, or best yet - something that falls in the outline of the logo icon, either fully or partially. Thank you, everyone!
Light for the Weary Souls text should be incorporated as well as a phone and email.

```html
<!DOCTYPE html>
<html lang="en">
<head>
<meta charset="utf-8">
<title>Light for the Weary Souls – Business Card</title>
<link href="https://fonts.googleapis.com/css2?family=Poppins:wght@400;500;600&display=swap" rel="stylesheet">
<style>
  :root {
    --page: #ffffff;
    --card-top: #fdf9f6;
    --card-bottom: #f8dcd3;
    --ink: #1b1b1b;
    --brand-red: #e0262b;
    --brand-crimson: #d81e4d;
    --brand-orange: #ef6a25;
    --icon-ring: #f3c9c4;
  }
  * { box-sizing: border-box; margin: 0; padding: 0; }
  html, body {
    width: 1200px; height: 400px; overflow: hidden;
    background: var(--page);
    font-family: "Poppins", sans-serif;
    color: var(--ink);
  }
  .sheet { position: relative; width: 1200px; height: 400px; }
  .card { position: absolute; top: 64px; width: 482px; height: 275px; }
  .card--front { left: 62px; }
  .card--back { left: 665px; }
  .card__shape {
    position: absolute; inset: 0; width: 482px; height: 275px;
    filter: drop-shadow(5px 7px 5px rgba(0,0,0,0.12));
  }
  .brand-tag {
    position: absolute; display: flex; align-items: center; gap: 6px;
    font-weight: 500; color: var(--brand-red); line-height: 1.15;
  }
  .brand-tag__dot { border-radius: 50%; background: var(--brand-red); flex: none; }
  .card--front .brand-tag { left: 41px; top: 58px; font-size: 13px; }
  .card--front .brand-tag__dot { width: 14px; height: 14px; }
  .card--back .brand-tag { left: 58px; top: 50px; font-size: 10px; }
  .card--back .brand-tag__dot { width: 11px; height: 11px; }
  .front-title {
    position: absolute; left: 41px; top: 132px;
    font-size: 22px; font-weight: 400; line-height: 1.05;
  }
  .front-title__accent { color: var(--brand-red); font-weight: 500; }
  .brand-feature {
    position: absolute; left: 232px; top: 56px; width: 200px;
    font-weight: 600; font-size: 33px; line-height: 1.08;
    color: var(--brand-red); letter-spacing: -0.5px;
  }
  .contact-name {
    position: absolute; left: 28px; top: 126px;
    font-size: 16px; font-weight: 600; color: var(--brand-crimson);
  }
  .contact-role {
    position: absolute; left: 28px; top: 145px;
    font-size: 14.5px; font-weight: 400;
  }
  .contact-line {
    position: absolute; left: 28px; display: flex; align-items: center; gap: 10px;
    font-size: 10.5px;
  }
  .contact-line--phone { top: 188px; }
  .contact-line--email { top: 214px; }
  .contact-line__icon {
    width: 15px; height: 15px; border-radius: 50%;
    border: 1px solid var(--icon-ring); background: #fff;
    display: flex; align-items: center; justify-content: center; flex: none;
  }
</style>
</head>
<body>
<main class="sheet">
  <svg width="0" height="0" style="position:absolute">
    <defs>
      <linearGradient id="card-fill" x1="0" y1="0" x2="0" y2="1">
        <stop offset="0" stop-color="#fdf9f6"/>
        <stop offset="1" stop-color="#f8dcd3"/>
      </linearGradient>
    </defs>
  </svg>

  <section class="card card--front" aria-label="Card front">
    <svg class="card__shape" viewBox="0 0 482 275" aria-hidden="true">
      <path d="M52 0 H341 A141 137.5 0 0 1 341 275 H52 A52 52 0 0 1 0 223 V52 A52 52 0 0 1 52 0 Z" fill="url(#card-fill)"/>
    </svg>
    <div class="brand-tag"><span class="brand-tag__dot"></span><span>Light for the<br>Weary Souls</span></div>
    <h1 class="front-title">Light for the<br><span class="front-title__accent">Weary Souls</span></h1>
    <div class="brand-feature">Light for the Weary Souls</div>
  </section>

  <section class="card card--back" aria-label="Card back">
    <svg class="card__shape" viewBox="0 0 482 275" aria-hidden="true">
      <path d="M52 0 H341 A141 137.5 0 0 1 341 275 H52 A52 52 0 0 1 0 223 V52 A52 52 0 0 1 52 0 Z" fill="url(#card-fill)"/>
    </svg>
    <div class="brand-tag"><span class="brand-tag__dot"></span><span>Light for the<br>Weary Souls</span></div>
    <h2 class="contact-name">Dana Whitfield</h2>
    <p class="contact-role">Marketing Director</p>
    <p class="contact-line contact-line--phone">
      <span class="contact-line__icon">
        <svg width="9" height="9" viewBox="0 0 24 24" aria-hidden="true"><path fill="#e0262b" d="M6.6 10.8a15 15 0 0 0 6.6 6.6l2.2-2.2c.3-.3.7-.4 1-.2 1.1.4 2.3.6 3.6.6.6 0 1 .4 1 1V20c0 .6-.4 1-1 1A17 17 0 0 1 3 4c0-.6.4-1 1-1h3.5c.6 0 1 .4 1 1 0 1.3.2 2.5.6 3.6.1.3 0 .7-.2 1z"/></svg>
      </span>555-382-7194
    </p>
    <p class="contact-line contact-line--email">
      <span class="contact-line__icon">
        <svg width="9" height="9" viewBox="0 0 24 24" aria-hidden="true"><rect x="2" y="5" width="20" height="14" rx="1.5" fill="#e0262b"/><path d="M3 6l9 7 9-7" fill="none" stroke="#fff" stroke-width="1.6"/></svg>
      </span>email@lightfortheweary-mail.org
    </p>
    <div class="brand-feature">Light for the Weary Souls</div>
  </section>
</main>
</body>
</html>
```